Seeking funky, innovative business cards

I am looking to refresh our current business cards to something more engaging, visual and impactful. We are a management consultancy firm, see website (www.larkstone-partners.com.au). I've included our colour scheme, sample of the slides we use and our old business cards. We would like our cards to have icons. The card should display:- Name- Title- Mobile number- Address- Email address- Website - Company logo- Our purpose statement "We create the best places on earth to work"

Contact Information for Business Card

Brennan Ulfsson
Consultant
0468 927 341
Level 3, 218 Wexley Street, Melbourne 3000
brennan@larkstone-partners.com.au
www.larkstone-partners.com.au

Purpose statement "we create the best places on earth to work"
LOGO available in google images

Font styles to use
Other font styles liked:
• Open Sans Light, Bebas Neue (open to other cool foints)

Colors
ffc214
5c5c5c
f5f5f5
fefefe

Requirements
Must have
• - Name
• - Title
• - Mobile number
• - Address
• - Email address
• - Website
• - Company logo
• - Our purpose statement "We create the best places on earth to work"
Nice to have
• - Icons
• - Colour (see our colour scheme"

```html
<!DOCTYPE html>
<html lang="en">
<head>
<meta charset="utf-8">
<title>Larkstone Partners – Business Card</title>
<link href="https://fonts.googleapis.com/css2?family=Lato:wght@300;400;700&display=swap" rel="stylesheet">
<style>
  :root {
    --stage: #161616;
    --card: #262626;
    --card-edge: #2e2e2e;
    --accent: #ffc214;
    --accent-deep: #f7a81b;
    --text: #fefefe;
    --text-soft: #f5f5f5;
    --muted: #8a8a8a;
  }
  * { box-sizing: border-box; margin: 0; padding: 0; }
  html, body {
    width: 1200px; height: 900px; overflow: hidden;
    background: var(--stage);
    font-family: "Lato", Arial, sans-serif;
  }
  .canvas { position: relative; width: 1200px; height: 900px; }
  .card {
    position: absolute; left: 250px; width: 700px; height: 400px;
    background: linear-gradient(135deg, var(--card) 0%, var(--card-edge) 100%);
    box-shadow: 0 14px 30px rgba(0,0,0,.55);
    overflow: hidden;
  }
  .card--back { top: 40px; }
  .card--front { top: 470px; }

  .pattern-field {
    position: absolute; inset: 0;
    background: radial-gradient(ellipse at 70% 40%, #343434 0%, #262626 70%);
  }
  .back-mark {
    position: absolute; left: 50%; top: 50%; transform: translate(-50%, -50%);
    display: flex; flex-direction: column; align-items: center; gap: 12px;
  }
  .back-name {
    display: flex; align-items: center; gap: 8px;
    color: var(--text); font-weight: 300; font-size: 18px; letter-spacing: .5px;
  }
  .purpose {
    color: var(--muted); font-weight: 300; font-size: 13px; letter-spacing: 1px;
  }
  .dot { width: 10px; height: 10px; border-radius: 50%; background: var(--accent); }

  .brand {
    position: absolute; left: 44px; top: 124px;
    display: flex; align-items: center; gap: 14px;
  }
  .brand .dot { width: 20px; height: 20px; }
  .brand-name {
    color: var(--text); font-weight: 300; font-size: 50px; line-height: 1;
  }
  .divider {
    position: absolute; left: 352px; top: 112px; width: 2px; height: 180px;
    background: var(--accent);
  }
  .details { position: absolute; left: 378px; top: 106px; color: var(--text-soft); }
  .person-name {
    color: var(--accent); font-weight: 700; font-size: 22px; letter-spacing: 2px;
    text-transform: uppercase;
  }
  .person-title { font-size: 15px; font-weight: 400; margin-top: 2px; }
  .address { font-size: 15px; line-height: 1.3; margin-top: 14px; }
  .contacts { list-style: none; margin-top: 12px; font-size: 15px; }
  .contacts li { display: flex; align-items: center; gap: 10px; line-height: 1.55; white-space: nowrap; }
  .contacts svg { width: 12px; height: 12px; flex: none; }
</style>
</head>
<body>
<main class="canvas">
  <section class="card card--back">
    <div class="pattern-field" role="img" aria-label="Subtle embossed repeating brand pattern on dark stock"></div>
    <div class="back-mark">
      <span class="back-name"><span class="dot"></span>Larkstone Partners</span>
      <p class="purpose">We create the best places on earth to work</p>
    </div>
  </section>

  <section class="card card--front">
    <div class="brand">
      <span class="dot"></span>
      <span class="brand-name">Larkstone<br>Partners</span>
    </div>
    <div class="divider"></div>
    <div class="details">
      <p class="person-name">Brennan Ulfsson</p>
      <p class="person-title">Consultant</p>
      <p class="address">Level 3, 218 Wexley Street<br>Melbourne, VIC 3000</p>
      <ul class="contacts">
        <li>
          <svg viewBox="0 0 12 12"><path d="M2.5 1l2 2.2-1 1.2c.7 1.4 1.8 2.5 3.2 3.2l1.2-1 2.1 2-1 1.4C5.6 10 2 6.4 1.1 2z" fill="var(--accent)"/></svg>
          0468 927 341
        </li>
        <li>
          <svg viewBox="0 0 12 12"><rect x="3" y="1" width="6" height="3" fill="var(--accent)"/><rect x="1" y="4.5" width="10" height="4.5" rx="1" fill="var(--accent)"/><rect x="3" y="8" width="6" height="3" fill="var(--accent-deep)"/></svg>
          +61 3 9274 6631
        </li>
        <li>
          <svg viewBox="0 0 12 12"><rect x="1" y="2.5" width="10" height="7" fill="none" stroke="var(--accent)"/><path d="M1 2.5l5 4 5-4" fill="none" stroke="var(--accent)"/></svg>
          brennan@larkstone-partners.com.au
        </li>
        <li>
          <svg viewBox="0 0 12 12"><circle cx="6" cy="6" r="5" fill="none" stroke="var(--accent)"/><ellipse cx="6" cy="6" rx="2.2" ry="5" fill="none" stroke="var(--accent)"/><path d="M1 6h10" stroke="var(--accent)"/></svg>
          www.larkstone-partners.com.au
        </li>
      </ul>
    </div>
  </section>
</main>
</body>
</html>
```